Website for 3d printing & other services

Hi, i'm after a website to sell my 3d printed automotive parts as well as sell my 3d printing services & other services.

There's a few things i need the website to have:

- Automatic 3d print quoting based on the file the client uploads to the website.
- Shop function where i can sell my custom automotive parts
- 3D printing technologies offered are SLA & FDM
- My business can offer 3d printing, 3d scanning, 3d cad design, cnc machining, steel fabrication, drafting services.

The color design is to suit my logo which is Black, orange & white.

Target Market(s)

3d printing, automotive, fabrication

Industry/Entity Type

General manufacturing & Custom automotive parts

Coding

Coded - Design and coding required

Number of Pages Required

5+ page

Requirements
Must have
• Automatic 3d print quoting. Shop for my printed parts.

```html
<!DOCTYPE html>
<html lang="en">
<head>
<meta charset="UTF-8">
<title>Arcline Draft &amp; Design</title>
<link href="https://fonts.googleapis.com/css2?family=Open+Sans:wght@300;400;600;700;800&display=swap" rel="stylesheet">
<style>
:root{
  --orange:#ff6a00;
  --ink:#111111;
  --night:#130806;
  --white:#ffffff;
  --steel:#3d4c60;
  --mist:#e9eaec;
  --text-grey:#555555;
}
*{margin:0;padding:0;box-sizing:border-box}
html,body{width:1200px;height:3327px;overflow:hidden;background:var(--white)}
body{position:relative;font-family:'Open Sans',Arial,sans-serif;color:var(--ink)}
.abs{position:absolute}
.pill{display:flex;align-items:center;justify-content:center;border-radius:30px;font-weight:600;color:var(--white)}
.pill-solid{background:var(--orange)}
.accent{position:absolute;height:4px;background:var(--orange)}

/* hero */
.hero-photo{left:0;top:0;width:1200px;height:600px;background:linear-gradient(100deg,#1b2636 0%,#2f3d52 45%,#6f7f94 75%,#4a586c 100%)}
.brand{left:98px;top:30px;color:var(--orange);font-weight:800;font-size:22px;line-height:26px;display:flex;align-items:center;gap:10px}
.brand-dot{width:14px;height:14px;border-radius:50%;background:var(--orange);flex:none}
.menu{left:1062px;top:52px;width:38px}
.menu span{display:block;height:4px;background:var(--orange);border-radius:2px;margin-bottom:10px}
.hero-rule{left:98px;top:177px;width:4px;height:199px;background:var(--orange)}
.hero-welcome{left:125px;top:170px;color:var(--white);font-size:22px}
.hero-title{left:125px;top:214px;color:var(--white);font-size:46px;font-weight:700;letter-spacing:.5px}
.hero-lead{left:125px;top:290px;width:460px;color:var(--white);font-size:16px;line-height:25px}
.hero-cta{left:103px;top:404px;width:162px;height:57px;font-size:19px}

/* automotive */
.auto-photo{left:98px;top:645px;width:480px;height:480px;border-radius:50%;background:radial-gradient(circle at 40% 40%,#c9d3e2 0%,#6a7c98 45%,#1f2a3c 100%);box-shadow:8px 10px 0 var(--orange)}
.auto-title{left:653px;top:646px;font-size:39px;font-weight:700;line-height:52px}
.auto-text{left:655px;top:778px;width:440px;font-size:14.5px;font-weight:300;line-height:24px;color:var(--text-grey)}
.auto-cta{left:657px;top:1054px;width:162px;height:57px;font-size:19px}

/* technologies */
.tech-photo{left:0;top:1227px;width:1200px;height:775px;background:linear-gradient(180deg,#dcdee2 0%,#e8e9eb 60%,#eeeff0 100%)}
.section-title{left:0;width:1200px;text-align:center;font-size:39px;font-weight:700}
.tech-card{top:1453px;width:486px;height:266px;border-radius:6px}
.tech-sla{left:98px;background:#120b08;padding:14px}
.tech-sla-inner{width:100%;height:100%;background:#2a1a12;border-radius:3px;padding:18px 16px;color:var(--white);font-size:15.5px;font-weight:700;line-height:25.7px;position:relative}
.tech-sla-inner svg{position:absolute;right:16px;bottom:12px}
.tech-fdm{left:616px;background:linear-gradient(135deg,#1c3f7a 0%,#5d7fb6 45%,#2a2e36 100%)}
.tech-label{top:1728px;width:486px;text-align:center;font-size:38px;font-weight:700}

/* business */
.tile{width:239px;height:176px;border-radius:4px}
.tile-label{width:239px;text-align:center;font-size:21px;font-weight:700;letter-spacing:.3px}

/* footer */
.footer-brand{left:103px;top:3000px;width:420px;color:var(--orange);font-weight:800;font-size:42px;line-height:54px;display:flex;align-items:center;gap:16px}
.footer-brand .brand-dot{width:24px;height:24px}
.copyright{left:103px;top:3252px;color:var(--white);font-size:16.5px}
.quote-title{left:670px;top:2846px;color:var(--white);font-size:36px;font-weight:700}
.quote-lead{left:671px;top:2902px;width:320px;color:var(--white);font-size:16px;font-weight:600;line-height:27px}
.field{background:var(--white);border-radius:2px;display:flex;align-items:center;justify-content:space-between;padding:0 14px;font-size:12.5px;color:#666}
.field-area{align-items:flex-start;padding-top:14px}
.submit{left:669px;top:3227px;width:158px;height:51px;font-size:19px}
.uploads{left:850px;top:3227px;width:220px;height:51px;font-size:19px;border:2px solid var(--white);gap:22px}
</style>
</head>
<body>

<!-- hero -->
<div class="abs hero-photo" role="img" aria-label="Photo of a 3D printer nozzle printing a dark lattice part"></div>
<svg class="abs" style="left:0;top:0" width="1200" height="3327" aria-hidden="true">
  <polygon points="0,600 965,501 1200,588 1200,610 0,610" fill="#ffffff"/>
  <polyline points="0,600 965,501 1200,588" fill="none" stroke="#ff6a00" stroke-width="5"/>
</svg>
<div class="abs brand"><span class="brand-dot"></span><span>ARCLINE<br>DRAFT &amp; DESIGN</span></div>
<div class="abs menu"><span></span><span></span><span></span></div>
<div class="abs hero-rule"></div>
<p class="abs hero-welcome">Welcome to</p>
<h1 class="abs hero-title">ARCLINE DRAFT &amp; DESIGN</h1>
<p class="abs hero-lead">Sed ut perspiciatis unde omnis iste natus error sitvoluptatem accusantium doloremque laudantium, totam rem aperiam, eaque ipsa quae ab illo inventore .</p>
<a class="abs pill pill-solid hero-cta">Get Started</a>

<!-- custom automotive parts -->
<div class="abs auto-photo" role="img" aria-label="Photo of a hand reaching toward a 3D printed hand on a printer bed"></div>
<div class="accent" style="left:655px;top:634px;width:97px"></div>
<h2 class="abs auto-title">CUSTOM AUTOMOTIVE<br>PARTS</h2>
<p class="abs auto-text">Sed ut perspiciatis unde omnis iste natus error sitvoluptatem accusantium doloremque laudantium, totam rem aperiam, eaque ipsa quae ab illo inventore veritatis et quasi architecto beatae vitae dicta sunt explicabo. Nemo enim ipsam voluptatem quia voluptas sit aspernatur aut odit aut fugit, sed quia consequuntur magni dolores eos qui ratione voluptatem sequi nesciunt. Neque porro quisquam est, qui dolorem ipsum quia dolor sit amet, consectetur, adipisci velit, sed quia non numquam eius modi tempora incidunt ut labore et dolore magnam aliquam quaerat voluptatem.</p>
<a class="abs pill pill-solid auto-cta">Shop Now</a>

<!-- 3d printing technologies -->
<div class="abs tech-photo" role="img" aria-label="Faded photo of engineers working in a print workshop"></div>
<svg class="abs" style="left:0;top:1880px" width="1200" height="140" aria-hidden="true">
  <polygon points="0,107 238,16 1200,120 1200,140 0,140" fill="#ffffff"/>
  <polyline points="0,107 238,16 1200,120" fill="none" stroke="#ff6a00" stroke-width="5"/>
</svg>
<div class="accent" style="left:552px;top:1320px;width:95px"></div>
<h2 class="abs section-title" style="top:1336px">3D PRINTING TECHNOLOGIES</h2>
<div class="abs tech-card tech-sla">
  <div class="tech-sla-inner">Lorem ipsum dolor sit amet, consectetur adipiscing elit, sed do eiusmod tempor incididunt ut labore et dolore magna aliqua. Ut enim ad minim veniam, quis nostrud exercitation ullamco laboris nisi ut aliquip ex ea commodo consequat. Lorem ipsum dolor sit amet, consectetur adipiscing elit, sed do eiusmod tempor incididunt ut labore et dolore magna aliqua. laboris nisi ut aliquip ex ea commodo consequat.
    <svg width="20" height="18" viewBox="0 0 20 18" aria-hidden="true"><path d="M3 9a7 7 0 0 1 12-4M17 9a7 7 0 0 1-12 4" fill="none" stroke="#fff" stroke-width="1.6"/><path d="M15 1v4h-4M5 17v-4h4" fill="none" stroke="#fff" stroke-width="1.6"/></svg>
  </div>
</div>
<div class="abs tech-card tech-fdm" role="img" aria-label="Photo of a desktop FDM printer with filament spool"></div>
<p class="abs tech-label" style="left:98px">SLA</p>
<p class="abs tech-label" style="left:616px">FDM</p>

<!-- my business -->
<div class="accent" style="left:552px;top:2052px;width:95px"></div>
<h2 class="abs section-title" style="top:2068px">MY BUSINESS</h2>
<div class="abs tile" style="left:98px;top:2162px;background:linear-gradient(135deg,#0d3b66,#c2401a 60%,#1a1a1a)" role="img" aria-label="Photo of a 3D printer printing an orange part"></div>
<div class="abs tile" style="left:353px;top:2162px;background:linear-gradient(135deg,#8da0b8,#3a3d6e 55%,#a7a9b5)" role="img" aria-label="Photo of a handheld scanner scanning a wheel"></div>
<div class="abs tile" style="left:608px;top:2162px;background:linear-gradient(135deg,#9fb9cf,#3e6fa0 50%,#cfd8e0)" role="img" aria-label="Photo of a CAD model on a monitor"></div>
<div class="abs tile" style="left:863px;top:2162px;background:linear-gradient(135deg,#cfd4d8,#5d666e 50%,#e3e6e8)" role="img" aria-label="Photo of a CNC milling spindle cutting metal"></div>
<p class="abs tile-label" style="left:98px;top:2348px">3D PRINTING</p>
<p class="abs tile-label" style="left:353px;top:2348px">3D SCANNING</p>
<p class="abs tile-label" style="left:608px;top:2348px">3D CAD DESIGN</p>
<p class="abs tile-label" style="left:863px;top:2348px">CNC MACHINING</p>
<div class="abs tile" style="left:342px;top:2431px;background:linear-gradient(135deg,#c8cacd,#6e7276 50%,#b3b6b9)" role="img" aria-label="Photo of rolled steel coils in a warehouse"></div>
<div class="abs tile" style="left:611px;top:2431px;background:linear-gradient(135deg,#e7e9ec,#b5bcc6 55%,#3f4c6b)" role="img" aria-label="Photo of engineers reviewing drafting plans"></div>
<p class="abs tile-label" style="left:342px;top:2616px">STEEL FABRICATION</p>
<p class="abs tile-label" style="left:611px;top:2616px">DRAFTING SERVICES</p>

<!-- quote footer -->
<svg class="abs" style="left:0;top:2740px" width="1200" height="587" aria-hidden="true">
  <polygon points="0,134 965,15 1200,121 1200,587 0,587" fill="#130806"/>
  <polyline points="0,134 965,15 1200,121" fill="none" stroke="#ff6a00" stroke-width="6"/>
</svg>
<div class="abs footer-brand"><span class="brand-dot"></span><span>ARCLINE<br>DRAFT &amp; DESIGN</span></div>
<p class="abs copyright">© copyrights 2023 Arcline Draft Design |&nbsp; All Rights Reserved</p>

<h2 class="abs quote-title">GET A QUOTE</h2>
<p class="abs quote-lead">Request a call from us to discuss our services &amp; price estimation</p>
<div class="abs field" style="left:672px;top:2976px;width:197px;height:44px">First Name
  <svg width="11" height="12" viewBox="0 0 11 12" aria-hidden="true"><circle cx="5.5" cy="3.5" r="3" fill="#777"/><path d="M0 12c0-4 2.5-5 5.5-5s5.5 1 5.5 5z" fill="#777"/></svg></div>
<div class="abs field" style="left:885px;top:2976px;width:198px;height:44px">Last Name
  <svg width="11" height="12" viewBox="0 0 11 12" aria-hidden="true"><circle cx="5.5" cy="3.5" r="3" fill="#777"/><path d="M0 12c0-4 2.5-5 5.5-5s5.5 1 5.5 5z" fill="#777"/></svg></div>
<div class="abs field" style="left:672px;top:3038px;width:197px;height:44px">Phone No
  <svg width="12" height="12" viewBox="0 0 12 12" aria-hidden="true"><path d="M2 1l2 0 1 3-1.5 1a7 7 0 0 0 3.5 3.5L8 7l3 1v2a1 1 0 0 1-1 1A10 10 0 0 1 1 2a1 1 0 0 1 1-1z" fill="#777"/></svg></div>
<div class="abs field" style="left:885px;top:3038px;width:198px;height:44px">Services
  <svg width="10" height="6" viewBox="0 0 10 6" aria-hidden="true"><path d="M0 0h10L5 6z" fill="#777"/></svg></div>
<div class="abs field field-area" style="left:672px;top:3097px;width:409px;height:99px">Additional Comments or Preferences
  <svg width="13" height="11" viewBox="0 0 13 11" aria-hidden="true"><path d="M1 1h11v6H5l-3 3V7H1z" fill="none" stroke="#777" stroke-width="1.2"/></svg></div>
<a class="abs pill pill-solid submit">Submit Now</a>
<a class="abs pill uploads">Client Uploads
  <svg width="18" height="17" viewBox="0 0 18 17" aria-hidden="true"><path d="M9 0l6 6h-4v6H7V6H3z" fill="#fff"/><path d="M0 11h5v2h8v-2h5v6H0z" fill="#fff"/></svg></a>

</body>
</html>
```